Lumbra Ember Oven Kitchen (restaurant)

Restaurant with a cool vibe.
We need a refresh of existing site. Appealing to a hip crowd of 25 or older age bracket (mid price to high small town). Constant changes food and cocktail menu. A vibing atmosphere with jazz funk hip music.
Must be able to scale for any device… phone/mobile device super important.
Instagram: @Lumbra.Bexwell
Website: lumbrabexwell.example

Target Market(s)

25-55 age group

Number of Pages Required

1 page

Font styles to use
Sans Serif

Requirements
Must have
• Simple to navigate. Simplicity is the key to all sophistication.

Links/Buttons
Menu
Gift Cards
Reservations
Take Out
Contact Us
Should not have
• Please, nothing generic looking… no cookie cutter look. Originality

```html
<!DOCTYPE html>
<html lang="en">
<head>
<meta charset="utf-8">
<title>Lumbra Ember Oven Kitchen</title>
<link rel="stylesheet" href="https://fonts.googleapis.com/css2?family=Poppins:wght@400;500&family=Rajdhani:wght@700&family=Bitter:wght@700&family=Quicksand:wght@500;600&display=swap">
<style>
:root{
  --yellow:#ffcc2f;
  --price:#d9600a;
  --ink:#1b1b1b;
  --dark:#1f1f1f;
  --white:#ffffff;
  --muted:#555555;
  --soft:#cfcfcf;
}
*{box-sizing:border-box;margin:0;padding:0}
html,body{width:1200px;height:2816px;overflow:hidden}
body{position:relative;background:var(--white);font-family:"Poppins",sans-serif;color:var(--ink)}

/* hero */
.hero{position:absolute;left:0;top:0;width:1200px;height:636px;overflow:hidden;
  background:
    radial-gradient(ellipse 420px 260px at 300px 330px,rgba(176,120,70,.75) 0%,rgba(176,120,70,0) 100%),
    radial-gradient(ellipse 520px 220px at 520px 520px,rgba(120,110,60,.7) 0%,rgba(120,110,60,0) 100%),
    radial-gradient(ellipse 300px 120px at 180px 150px,rgba(140,150,160,.45) 0%,rgba(140,150,160,0) 100%),
    radial-gradient(ellipse 360px 260px at 950px 120px,rgba(80,90,110,.45) 0%,rgba(80,90,110,0) 100%),
    linear-gradient(180deg,#2a2a2e 0%,#3b2f25 55%,#4a3a28 100%);}
.hero-shade{position:absolute;inset:0;background:linear-gradient(90deg,rgba(10,12,20,.05) 0%,rgba(10,12,20,.35) 60%,rgba(10,12,20,.5) 100%)}
.brand{position:absolute;left:60px;top:14px;color:var(--white);font-family:"Quicksand",sans-serif;font-weight:600;line-height:1}
.brand .name{font-size:30px;letter-spacing:1px;display:block}
.brand .tag{font-size:10px;display:block;margin-top:2px;padding-left:16px}
.nav{position:absolute;top:26px;right:58px;display:flex;gap:32px;font-size:12px;color:var(--white)}
.nav .active{color:var(--yellow)}
.hero-kicker{position:absolute;right:62px;top:182px;font-family:"Quicksand",sans-serif;font-weight:500;font-size:23px;color:var(--yellow)}
.hero-title{position:absolute;right:62px;top:228px;text-align:right;font-family:"Rajdhani",sans-serif;font-weight:700;font-size:74px;line-height:84px;color:var(--white)}
.btn{position:absolute;height:38px;display:flex;align-items:center;justify-content:center;font-family:"Bitter",serif;font-weight:700;font-size:14px;letter-spacing:.5px;border-radius:4px}
.btn-solid{background:var(--yellow);color:var(--ink)}
.btn-line{border:1.5px solid var(--yellow);color:var(--white)}

/* menu */
.section-title{position:absolute;left:0;width:1200px;text-align:center;font-family:"Rajdhani",sans-serif;font-weight:700;font-size:33px;color:var(--ink)}
.menu-col{position:absolute;top:784px}
.menu-col h3{font-family:"Quicksand",sans-serif;font-weight:600;font-size:22px;color:var(--ink);margin-bottom:36px}
.dish{height:76px}
.dish .n{font-size:13.5px;color:var(--muted);letter-spacing:.2px}
.dish .p{font-size:17px;color:var(--price);margin-top:3px}
.salad-art{position:absolute;left:770px;top:690px;width:430px;height:556px;
  background:radial-gradient(ellipse at 60% 75%,#cfe3b9 0%,#e9f1dc 40%,rgba(255,255,255,0) 75%)}
.dots{position:absolute;top:1157px;left:350px;display:flex;gap:10px;align-items:center}
.dots span{width:11px;height:11px;border:1.5px solid #444;border-radius:50%}
.dots span.on{background:radial-gradient(circle,#444 45%,transparent 50%)}
.dots span.sm{width:8px;height:8px}

/* reservation */
.reserve{position:absolute;left:0;top:1246px;width:1200px;height:446px;background:var(--dark);overflow:hidden}
.pizza-left{position:absolute;left:-170px;top:60px;width:620px;height:440px;border-radius:50%;background:radial-gradient(circle at 55% 50%,#b0452c 0%,#8a3a24 45%,#c9a278 70%,#e6ddd0 72%)}
.plate-right{position:absolute;left:790px;top:-150px;width:560px;height:520px;border-radius:50%;background:radial-gradient(circle at 40% 45%,#e9c77f 0%,#d9d2c6 40%,#f3f3f3 60%)}
.reserve h2{position:absolute;left:0;top:104px;width:1200px;text-align:center;font-family:"Rajdhani",sans-serif;font-weight:700;font-size:35px;color:var(--white)}
.reserve p{position:absolute;left:390px;top:164px;width:420px;text-align:center;font-size:12.5px;line-height:20px;color:var(--white)}
.field{position:absolute;top:222px;width:244px;height:37px;background:var(--white);display:flex;align-items:center;font-size:12px;color:#777}
.field svg{margin:0 8px 0 9px}
.field .bar{width:1px;height:18px;background:#aaa;margin-right:8px}

/* contact */
.card{position:absolute;overflow:hidden}
.card-hours{left:124px;top:1845px;width:292px;height:235px;background:var(--ink);color:var(--white)}
.card-yellow{left:124px;top:2107px;width:292px;height:235px;background:var(--yellow);color:var(--ink)}
.card h4{font-family:"Quicksand",sans-serif;font-weight:600;font-size:21px;margin:0 0 14px}
.card .row{font-size:12.5px;height:39px}
.card-photo{top:1845px;width:300px;height:497px;display:flex;flex-direction:column;align-items:center;justify-content:center;color:var(--white);text-align:center}
.tacos{left:446px;background:radial-gradient(ellipse at 50% 45%,#7a6a48 0%,#4a4536 45%,#26261f 100%)}
.giftcard{left:776px;background:linear-gradient(160deg,#5b5249 0%,#3f3832 55%,#2a2622 100%)}
.card-photo h4{font-size:23px;margin-bottom:14px}
.card-photo .row{font-size:12.5px;height:39px}

/* footer */
.footer{position:absolute;left:0;top:2455px;width:1200px;height:323px;background:radial-gradient(ellipse at 65% 40%,#2d2a26 0%,#1a1a1b 60%,#121214 100%)}
.footer .brand{top:88px;left:60px}
.footer .brand .name{font-size:38px}
.footer .brand .tag{font-size:13px;padding-left:20px}
.foot-about{position:absolute;left:61px;top:162px;width:320px;font-size:12.5px;line-height:20px;color:var(--soft)}
.foot-h{position:absolute;top:80px;font-family:"Quicksand",sans-serif;font-weight:600;font-size:21px;color:var(--yellow)}
.foot-links{position:absolute;left:433px;top:118px;list-style:none;font-size:12.5px;color:var(--soft)}
.foot-links li{height:27px}
.foot-contact{position:absolute;left:804px;top:120px;font-size:12.5px;color:var(--white)}
.foot-contact .item{display:flex;align-items:center;height:52px}
.foot-contact svg{width:40px}
.copyright{position:absolute;left:0;top:2778px;width:1200px;height:38px;background:var(--yellow);display:flex;align-items:center;justify-content:center;font-size:12px;color:var(--ink)}
</style>
</head>
<body>

<header class="hero">
  <div class="hero-shade" role="img" aria-label="Photo of wood fired pizzas with fresh rocket on a kitchen counter"></div>
  <div class="brand"><span class="name">LUMBRA</span><span class="tag">Ember Oven Kitchen</span></div>
  <nav class="nav">
    <span class="active">Home</span><span>Area For Gift Cards</span><span>Menu</span><span>Contact Us</span><span>Reservations</span><span>Take Out</span>
  </nav>
  <div class="hero-kicker">Ember Oven Kitchen</div>
  <h1 class="hero-title">Lets Get Lunch At<br>Lumbra!</h1>
  <span class="btn btn-solid" style="left:825px;top:428px;width:149px">ORDER NOW</span>
  <span class="btn btn-line" style="left:990px;top:428px;width:150px">BOOK A TABLE</span>
</header>

<section class="menu">
  <h2 class="section-title" style="top:706px">OUR MENU</h2>
  <div class="salad-art" role="img" aria-label="Illustration of salad ingredients falling into a glass bowl"></div>
  <div class="menu-col" style="left:61px">
    <h3>Mains &amp; Pasta</h3>
    <div class="dish"><div class="n">Sonoma Valley Pasta</div><div class="p">$20.00</div></div>
    <div class="dish"><div class="n">Shrimp Linguine</div><div class="p">$25.00</div></div>
    <div class="dish"><div class="n">Chicken Souvlaki</div><div class="p">$25.00</div></div>
    <div class="dish"><div class="n">Buttermilk Fried Tenders</div><div class="p">$20.00</div></div>
  </div>
  <div class="menu-col" style="left:331px">
    <h3>Salad</h3>
    <div class="dish"><div class="n">Brussels Sprouts Salad</div><div class="p">$18.00</div></div>
    <div class="dish"><div class="n">Mill Valley Salad</div><div class="p">$18.00</div></div>
    <div class="dish"><div class="n">Butternut Squash Salad</div><div class="p">$18.00</div></div>
    <div class="dish"><div class="n">Sacramento Beet Salad</div><div class="p">$18.00</div></div>
  </div>
  <div class="menu-col" style="left:541px">
    <h3>Ember Oven Pizza</h3>
    <div class="dish"><div class="n">Big Sur</div><div class="p">$18.00</div></div>
    <div class="dish"><div class="n">The Barber</div><div class="p">$18.00</div></div>
    <div class="dish"><div class="n">Frank Across The Street</div><div class="p">$18.00</div></div>
    <div class="dish"><div class="n">Mushroom Bianco</div><div class="p">$18.00</div></div>
  </div>
  <div class="dots"><span class="on"></span><span></span><span class="sm"></span></div>
</section>

<section class="reserve">
  <div class="pizza-left" role="img" aria-label="Photo of a mushroom and pepperoni pizza"></div>
  <div class="plate-right" role="img" aria-label="Photo of a pizza slice on a plate with fork and knife"></div>
  <h2>MAKE A RESERVATION</h2>
  <p>Reservations will not be available for the courtyard under phase 1 and 2 of reopening. Walk-ins only. We can't wait to see you!</p>
  <div class="field" style="left:215px"><svg width="16" height="12" viewBox="0 0 16 12"><rect x=".5" y=".5" width="15" height="11" fill="none" stroke="#888"/><path d="M.5 .5 L8 7 L15.5 .5" fill="none" stroke="#888"/></svg><span class="bar"></span>Email</div>
  <div class="field" style="left:478px"><svg width="10" height="14" viewBox="0 0 10 14"><circle cx="5" cy="3" r="2.2" fill="#888"/><rect x="2.5" y="6" width="5" height="8" rx="1.5" fill="#888"/></svg><span class="bar"></span>Person</div>
  <div class="field" style="left:740px"><svg width="14" height="14" viewBox="0 0 14 14"><rect x=".5" y="2" width="13" height="11.5" fill="none" stroke="#888"/><rect x=".5" y="2" width="13" height="3" fill="#888"/></svg><span class="bar"></span>Date</div>
  <span class="btn btn-solid" style="left:525px;top:304px;width:150px;height:36px">BOOK TABLE</span>
</section>

<section class="contact">
  <h2 class="section-title" style="top:1764px">CONTACT US</h2>
  <div class="card card-hours" style="padding:34px 0 0 58px">
    <h4>Canada Day Hours!</h4>
    <div class="row">Thursday, July 1st &nbsp;- &nbsp;Open</div>
    <div class="row">Friday, July 2nd &nbsp;- &nbsp;Open</div>
    <div class="row">Saturday, July 3rd &nbsp;- &nbsp;Open</div>
    <div class="row">Sunday, July 4th &nbsp;- &nbsp;Closed</div>
  </div>
  <div class="card card-yellow" style="padding:52px 0 0 58px">
    <h4>Outdoor Dining Hours</h4>
    <div class="row">Our courtyard is open!</div>
    <div class="row">Thursday to Sunday</div>
    <div class="row">12:00pm - 9:00pm</div>
  </div>
  <div class="card card-photo tacos" role="img" aria-label="Photo of grilled chicken tacos with avocado">
    <h4>Takeout &amp; Kitchen Hours</h4>
    <div class="row">Thursday to Sunday</div>
    <div class="row">12:00pm - 8:00pm</div>
  </div>
  <div class="card card-photo giftcard" role="img" aria-label="Photo of a printed restaurant gift card">
    <h4 style="font-size:34px;margin-bottom:8px">Gift Card</h4>
    <div class="row">Offer Just For You</div>
  </div>
</section>

<footer class="footer" role="img" aria-label="Dim photo of a plated dish behind the footer">
  <div class="brand"><span class="name">LUMBRA</span><span class="tag">Ember Oven Kitchen</span></div>
  <p class="foot-about">Reservations will not be available for the courtyard Under phase 1 and 2 of reopening. Walk-ins only. We can't wait to see you!</p>
  <div class="foot-h" style="left:433px">Site Map</div>
  <ul class="foot-links">
    <li>- Home</li><li>- Area For Gift cards</li><li>- Menu</li><li>- Contact Us</li><li>- Reservation</li><li>- Tack Out</li>
  </ul>
  <div class="foot-h" style="left:804px">Contact Us</div>
  <div class="foot-contact">
    <div class="item"><svg height="20" viewBox="0 0 14 20"><path d="M7 0C3 0 0 3 0 7c0 5 7 13 7 13s7-8 7-13c0-4-3-7-7-7z" fill="#ffcc2f"/><circle cx="7" cy="7" r="2.6" fill="#1a1a1b"/></svg>48 Harrow Lane Bexwell, ON</div>
    <div class="item"><svg height="20" viewBox="0 0 20 20"><path d="M4 1l4 4-2 3c1 3 3 5 6 6l3-2 4 4-3 3C8 19 1 12 1 4z" fill="#ffcc2f"/></svg>555-014-2286</div>
    <div class="item"><svg height="16" viewBox="0 0 20 14"><rect width="20" height="14" fill="#ffcc2f"/><path d="M0 0 L10 8 L20 0" fill="none" stroke="#1a1a1b" stroke-width="1.5"/></svg>hello@lumbrabexwell.example</div>
  </div>
</footer>
<div class="copyright">© 2021 LUMBRA . All Rights Reserved.</div>

</body>
</html>
```